Brisk Fixwell business card

I need business card for my business, I think you have all my details.six months ago I design with you car wrap design. We would like to design both side of the card. On front of card we would like logo , Name and our contact details.
At the back we are looking to mentioned our services.
The name will be:
Faridoullan Mestor
Managing Director
Ph:07952338417
Email:info@brisk-fixwell.com
Web:www.brisk-fixwell.com
So we have our logo, you don’t need to change the logo.
Please see the attachment.
Thanks

Target Market(s)

Home improvement

Industry/Entity Type

Home Improvement

Contact Information for Business Card

Company name: Brisk Fixwell
Name: Faridoullan Mestor
Position: Director
Ph:07952338417
Web: www.brisk-fixwell.com
Add: 42 Corvale Road
Hounslow
TW3 9KD
SECOND PERSON
Nizamuddel mestor
Position: Handyman
Ph: 07812 564037
Email: info@brisk-fixwell.com
Add: 18 Brackwin Lane Road
Hounslow
TW6 2LB

```html
<!DOCTYPE html>
<html lang="en">
<head>
<meta charset="utf-8">
<title>Brisk Fixwell – Business Card</title>
<link rel="stylesheet" href="https://fonts.googleapis.com/css2?family=Fira+Sans:wght@400;500;700&family=Fira+Sans+Condensed:wght@700&display=swap">
<style>
  :root {
    --navy: #22387f;
    --red: #e31b2b;
    --grey: #9c9da0;
    --rule: #c9c9cc;
    --ink: #3a3a3c;
    --paper: #ffffff;
    --backdrop: #e8e8e9;
  }
  * { box-sizing: border-box; margin: 0; padding: 0; }
  html, body {
    width: 1200px; height: 1200px; overflow: hidden;
    background: var(--backdrop);
    font-family: "Fira Sans", Arial, sans-serif;
  }
  .sheet {
    position: relative; width: 1200px; height: 1200px;
    display: flex; flex-direction: column; align-items: center;
    justify-content: center; gap: 52px;
  }
  .card {
    position: relative; width: 900px; height: 514px;
    background: var(--paper);
    box-shadow: 0 6px 22px rgba(0,0,0,0.12);
    overflow: hidden;
  }
  .brand {
    position: absolute; display: flex; align-items: center; gap: 18px;
    color: var(--navy); font-weight: 700; letter-spacing: 0.5px;
    white-space: nowrap; line-height: 1;
  }
  .brand-mark {
    width: 30px; height: 30px; border-radius: 50%; background: var(--red); flex: none;
  }
  .card-front .brand { left: 240px; top: 70px; font-size: 62px; }
  .person {
    position: absolute; left: 200px; top: 168px;
  }
  .person-name {
    font-family: "Fira Sans Condensed", "Fira Sans", sans-serif;
    font-weight: 700; font-size: 30px; color: var(--navy);
    letter-spacing: 0.6px; text-transform: uppercase;
  }
  .person-role { font-size: 18px; color: var(--ink); margin-top: 2px; }
  .divider {
    position: absolute; left: 170px; right: 60px; top: 252px;
    height: 1px; background: var(--rule);
  }
  .contacts {
    position: absolute; left: 70px; top: 280px; list-style: none;
    display: flex; flex-direction: column; gap: 10px;
  }
  .contact, .address {
    display: flex; align-items: center; gap: 12px;
    font-size: 19px; color: var(--ink); white-space: nowrap;
  }
  .icon { width: 20px; height: 20px; flex: none; }
  .address {
    position: absolute; right: 60px; bottom: 86px;
    align-items: flex-end; text-align: right; line-height: 1.35;
  }
  .band { position: absolute; left: 0; bottom: 0; width: 900px; height: 44px; display: block; }
  .back-lockup {
    position: absolute; left: 0; right: 0; top: 160px;
    display: flex; flex-direction: column; align-items: center; gap: 22px;
  }
  .card-back .brand { position: static; font-size: 74px; }
  .web-link {
    color: var(--red); font-size: 26px; font-weight: 500; white-space: nowrap;
  }
</style>
</head>
<body>
<main class="sheet">

  <section class="card card-front" aria-label="Business card front">
    <div class="brand"><span class="brand-mark"></span>Brisk Fixwell</div>

    <div class="person">
      <p class="person-name">Faridoullan Mestor</p>
      <p class="person-role">Director</p>
    </div>

    <div class="divider"></div>

    <ul class="contacts">
      <li class="contact">
        <svg class="icon" viewBox="0 0 20 20"><circle cx="10" cy="10" r="10" fill="var(--navy)"/><path d="M6.5 5.5c.6-.6 1.3-.5 1.6 0l1 1.5c.3.5.2 1-.2 1.3l-.6.5c.5 1.2 1.5 2.2 2.7 2.7l.5-.6c.3-.4.8-.5 1.3-.2l1.5 1c.5.3.6 1 0 1.6-.9.9-2.3 1-4-.1-1.6-1-3-2.4-3.9-4-1-1.7-.9-3 0-3.7z" fill="#fff"/></svg>
        07952338417
      </li>
      <li class="contact">
        <svg class="icon" viewBox="0 0 20 20"><circle cx="10" cy="10" r="10" fill="var(--navy)"/><rect x="5" y="6.5" width="10" height="7" rx="1" fill="#fff"/><path d="M5.5 7l4.5 3.5L14.5 7" fill="none" stroke="var(--navy)" stroke-width="1.2"/></svg>
        info@brisk-fixwell.com
      </li>
      <li class="contact">
        <svg class="icon" viewBox="0 0 20 20"><circle cx="10" cy="10" r="10" fill="var(--navy)"/><g fill="none" stroke="#fff" stroke-width="1.2"><circle cx="10" cy="10" r="5"/><ellipse cx="10" cy="10" rx="2.2" ry="5"/><path d="M5 10h10"/></g></svg>
        www.brisk-fixwell.com
      </li>
    </ul>

    <div class="address">
      <p>42 Corvale Road<br>Hounslow, TW3 9KD</p>
      <svg class="icon" viewBox="0 0 20 20"><circle cx="10" cy="10" r="10" fill="var(--navy)"/><path d="M10 4.5a3.5 3.5 0 0 1 3.5 3.5c0 2.6-3.5 7-3.5 7s-3.5-4.4-3.5-7A3.5 3.5 0 0 1 10 4.5z" fill="#fff"/><circle cx="10" cy="8" r="1.3" fill="var(--navy)"/></svg>
    </div>

    <svg class="band" viewBox="0 0 900 44" preserveAspectRatio="none">
      <polygon points="0,0 540,0 528,44 0,44" fill="var(--navy)"/>
      <polygon points="552,0 742,0 730,44 540,44" fill="var(--red)"/>
      <polygon points="754,0 900,0 900,44 742,44" fill="var(--grey)"/>
    </svg>
  </section>

  <section class="card card-back" aria-label="Business card back">
    <div class="back-lockup">
      <div class="brand"><span class="brand-mark"></span>Brisk Fixwell</div>
      <p class="web-link">www.brisk-fixwell.com</p>
    </div>

    <svg class="band" viewBox="0 0 900 44" preserveAspectRatio="none">
      <polygon points="0,0 540,0 528,44 0,44" fill="var(--navy)"/>
      <polygon points="552,0 742,0 730,44 540,44" fill="var(--red)"/>
      <polygon points="754,0 900,0 900,44 742,44" fill="var(--grey)"/>
    </svg>
  </section>

</main>
</body>
</html>
```